Brisk Harbor claims recovery services

Its a new company in Dubai UAE. The company activity is debt management, debt collection, loans settlements and restructuring. The company involved in any business or sector requires debt management including government entities, Medical & Health care sector, Banks & finance companies, SME's and commercial business.

Target Market(s)

government entities, Medical & Health care sector, Banks & finance companies, SME's and commercial business.

Industry/Entity Type

Financial Service

Number of Pages Required

5+ page

Requirements
Must have
• Focus on the services not the team and clients
Should not have
• Colorful . Shouldn't have Client testimonial and our clients

```html
<!DOCTYPE html>
<html lang="en">
<head>
<meta charset="utf-8">
<title>Brisk Harbor — Claims Recovery Services</title>
<link rel="stylesheet" href="https://fonts.googleapis.com/css2?family=Cinzel:wght@400;700&family=Lato:wght@900&family=Open+Sans:wght@400;600;700&family=Roboto+Condensed:wght@400&display=swap">
<style>
  :root {
    --brand: #27527a;
    --brand-dark: #1f4468;
    --grey-text: #8c8c8c;
    --body-text: #5a5a5a;
    --band: #eeeeee;
    --line: #d6d6d6;
    --white: #ffffff;
  }
  * { box-sizing: border-box; margin: 0; padding: 0; }
  html, body { width: 1098px; height: 1200px; overflow: hidden; background: var(--white); }
  body { position: relative; font-family: "Open Sans", sans-serif; color: var(--body-text); }

  .site-header { position: absolute; top: 0; left: 0; width: 1098px; height: 117px; }
  .brand { position: absolute; left: 72px; top: 36px; display: flex; align-items: center; gap: 12px; }
  .brand-mark { width: 34px; height: 34px; background: var(--brand); }
  .brand-name { font-family: "Cinzel", serif; font-size: 32px; color: var(--brand); letter-spacing: 1px; }
  .main-nav { position: absolute; right: 74px; top: 44px; display: flex; gap: 36px; }
  .main-nav a { font-family: "Cinzel", serif; font-size: 17px; color: var(--grey-text); text-decoration: none; letter-spacing: 0.5px; }
  .main-nav a.is-active { color: var(--brand); }

  .hero { position: absolute; top: 117px; left: 0; width: 1098px; height: 499px; overflow: hidden; }
  .hero-photo { position: absolute; inset: 0;
    background: linear-gradient(100deg, #f4f4f4 0%, #ececec 35%, #cfcfd1 60%, #9c9b9c 80%, #6f6e70 100%); }
  .hero-title { position: absolute; left: 72px; top: 96px; font-family: "Lato", sans-serif; font-weight: 900;
    font-size: 40px; line-height: 57px; color: var(--brand); letter-spacing: -0.3px; }
  .hero-button { position: absolute; left: 71px; top: 287px; width: 181px; height: 57px;
    border: 1px solid var(--brand); border-radius: 2px; display: flex; align-items: center; justify-content: center;
    font-family: "Cinzel", serif; font-size: 21px; color: var(--brand); text-decoration: none; letter-spacing: 0.5px; }

  .service-card { position: absolute; top: 587px; width: 315px; height: 228px; background: var(--brand);
    border-radius: 4px; color: var(--white); text-align: center; }
  .service-card.recovery { left: 196px; }
  .service-card.debt { left: 587px; }
  .service-icon { position: absolute; left: 50%; top: -62px; width: 124px; height: 124px; margin-left: -62px; }
  .service-icon .diamond { position: absolute; left: 21px; top: 21px; width: 82px; height: 82px; background: var(--white);
    border: 2px solid var(--brand); border-radius: 6px; transform: rotate(45deg); }
  .service-icon svg { position: absolute; left: 37px; top: 37px; width: 50px; height: 50px; }
  .service-title { position: absolute; top: 84px; width: 100%; font-family: "Roboto Condensed", sans-serif; font-size: 25px; }
  .service-text { position: absolute; top: 122px; left: 12px; right: 12px; font-size: 15px; line-height: 23px; }

  .welcome { position: absolute; top: 862px; left: 0; width: 1098px; text-align: center; }
  .welcome-title { font-family: "Cinzel", serif; font-weight: 700; font-size: 44px; color: var(--grey-text); letter-spacing: 1px; }
  .welcome-title span { color: var(--brand); }
  .welcome-text { width: 870px; margin: 14px auto 0; font-size: 15px; line-height: 23px; color: var(--body-text); }

  .contact-band { position: absolute; top: 1038px; left: 0; width: 1098px; height: 114px; background: var(--band);
    border-top: 1px solid var(--line); }
  .contact-item { position: absolute; top: 19px; display: flex; align-items: center; gap: 11px; }
  .contact-item.location { left: 71px; }
  .contact-item.phone { left: 406px; }
  .contact-item.email { left: 741px; }
  .contact-icon { width: 76px; height: 76px; border: 1px solid #666; border-radius: 50%;
    display: flex; align-items: center; justify-content: center; }
  .contact-icon svg { width: 32px; height: 32px; }
  .contact-text { font-size: 15px; line-height: 23px; color: #666; }
  .contact-text.large { font-size: 20px; font-weight: 600; color: #555; }

  .site-footer { position: absolute; top: 1152px; left: 0; width: 1098px; height: 48px; background: var(--brand);
    color: var(--white); font-size: 15px; }
  .copyright { position: absolute; left: 72px; top: 13px; }
  .copyright strong { font-weight: 700; }
  .legal-links { position: absolute; right: 74px; top: 13px; }
  .legal-links a { color: var(--white); text-decoration: none; }
</style>
</head>
<body>
  <header class="site-header">
    <div class="brand"><span class="brand-mark"></span><span class="brand-name">BRISK HARBOR</span></div>
    <nav class="main-nav">
      <a href="#" class="is-active">HOME</a>
      <a href="#">ABOUT</a>
      <a href="#">SERVICES</a>
      <a href="#">CLIENTS</a>
      <a href="#">BLOG</a>
      <a href="#">CONTACT</a>
    </nav>
  </header>

  <section class="hero">
    <div class="hero-photo" role="img" aria-label="Desk with an open ledger book, a pen and a calculator in soft grey light"></div>
    <h1 class="hero-title">MANAGING YOUR MONEY,<br>RECOVERING YOUR<br>RELATIONSHIPS</h1>
    <a href="#" class="hero-button">CONTACT US</a>
  </section>

  <article class="service-card recovery">
    <div class="service-icon">
      <div class="diamond"></div>
      <svg viewBox="0 0 50 50" fill="#27527a">
        <g transform="translate(18 26)">
          <circle r="10"/>
          <g><rect x="-3" y="-15" width="6" height="30"/><rect x="-15" y="-3" width="30" height="6"/>
          <rect x="-3" y="-15" width="6" height="30" transform="rotate(45)"/><rect x="-3" y="-15" width="6" height="30" transform="rotate(-45)"/></g>
          <circle r="4.5" fill="#fff"/>
        </g>
        <g transform="translate(38 14)">
          <circle r="5.5"/><rect x="-2" y="-8.5" width="4" height="17"/><rect x="-8.5" y="-2" width="17" height="4"/>
          <rect x="-2" y="-8.5" width="4" height="17" transform="rotate(45)"/><rect x="-2" y="-8.5" width="4" height="17" transform="rotate(-45)"/>
          <circle r="2.5" fill="#fff"/>
        </g>
        <g transform="translate(38 37)">
          <circle r="5.5"/><rect x="-2" y="-8.5" width="4" height="17"/><rect x="-8.5" y="-2" width="17" height="4"/>
          <rect x="-2" y="-8.5" width="4" height="17" transform="rotate(45)"/><rect x="-2" y="-8.5" width="4" height="17" transform="rotate(-45)"/>
          <circle r="2.5" fill="#fff"/>
        </g>
      </svg>
    </div>
    <h2 class="service-title">Recovery Solutions</h2>
    <p class="service-text">Our experience has taught us that when it comes to recovery, it always pays to find...</p>
  </article>

  <article class="service-card debt">
    <div class="service-icon">
      <div class="diamond"></div>
      <svg viewBox="0 0 50 50" fill="#27527a">
        <rect x="19" y="3" width="12" height="11" rx="2"/>
        <rect x="23.5" y="14" width="3" height="10"/>
        <rect x="8" y="23" width="34" height="3"/>
        <rect x="8" y="23" width="3" height="10"/><rect x="23.5" y="23" width="3" height="10"/><rect x="39" y="23" width="3" height="10"/>
        <rect x="3" y="32" width="13" height="12" rx="2"/><rect x="18.5" y="32" width="13" height="12" rx="2"/><rect x="34" y="32" width="13" height="12" rx="2"/>
      </svg>
    </div>
    <h2 class="service-title">Debt Management</h2>
    <p class="service-text">At Brisk Harbor, we pull together our wisdom and expertise to make debt work for you.</p>
  </article>

  <section class="welcome">
    <h2 class="welcome-title">WELCOME TO <span>BRISK HARBOR</span></h2>
    <p class="welcome-text">We are a Claims Recovery and Debt Management Services company based in Dubai, United Arab Emirates. The Brisk Harbor team handles a comprehensive range of debt recoveries, such as invoices; insurance payments; supplier and rent payments; and personal and business loans, for individuals and businesses across an array of industries.</p>
  </section>

  <section class="contact-band">
    <div class="contact-item location">
      <div class="contact-icon">
        <svg viewBox="0 0 32 32"><path d="M16 3a9 9 0 0 0-9 9c0 7 9 17 9 17s9-10 9-17a9 9 0 0 0-9-9z" fill="#27527a"/><circle cx="16" cy="12" r="3.5" fill="#eee"/></svg>
      </div>
      <p class="contact-text">Lorem Ipsum is simply<br>dummy text.</p>
    </div>
    <div class="contact-item phone">
      <div class="contact-icon">
        <svg viewBox="0 0 32 32"><path d="M9 3l5 6-3 3c1.5 3.5 5.5 7.5 9 9l3-3 6 5-3 5C15 28 4 17 4 6z" fill="#27527a"/></svg>
      </div>
      <p class="contact-text large">123 456 7890</p>
    </div>
    <div class="contact-item email">
      <div class="contact-icon">
        <svg viewBox="0 0 32 32" fill="none" stroke="#27527a" stroke-width="2.5"><rect x="3" y="7" width="26" height="18" rx="2"/><path d="M4 9l12 9 12-9"/></svg>
      </div>
      <p class="contact-text">info@briskharbor.com</p>
    </div>
  </section>

  <footer class="site-footer">
    <p class="copyright">© <strong>BRISK HARBOR</strong> - 2016. All Rights Reserved.</p>
    <p class="legal-links"><a href="#">Terms &amp; Condition</a> &nbsp;|&nbsp; <a href="#">Privacy Policy</a></p>
  </footer>
</body>
</html>
```